Sparrow Haulage needs a business card design.

Design a double-sided business card for new freight business. On the front, would like to see our logo along with the following info:

Martin Obuya
CEO/FOUNDER
555-206-7142
martinobuya@sparrow-haulage.example

On the reverse side, we would like to use the graphic image of our logo only without the Sparrow Haulage name.

```html
<!DOCTYPE html>
<html lang="en">
<head>
<meta charset="utf-8">
<title>Sparrow Haulage — Business Card</title>
<link rel="stylesheet" href="https://fonts.googleapis.com/css2?family=Montserrat:wght@700&family=Roboto:wght@400&display=swap">
<style>
  :root {
    --navy: #2b2a6e;
    --navy-deep: #16154a;
    --card-navy: #222066;
    --red: #c3272f;
    --edge-red: #9a0f14;
    --white: #ffffff;
    --paper: #f7f7f6;
    --ink: #4a4a4a;
  }
  * { box-sizing: border-box; margin: 0; padding: 0; }
  html, body {
    width: 1200px; height: 1050px; overflow: hidden;
    background: var(--navy-deep);
  }
  .canvas {
    position: relative; width: 1200px; height: 1050px;
  }
  .card {
    position: absolute; left: 250px; width: 700px; height: 400px;
    border-bottom: 4px solid var(--edge-red);
    box-shadow: 0 18px 40px rgba(0,0,0,0.35);
  }
  .card-front { top: 90px; background: var(--paper); }
  .card-back { top: 560px; background: var(--card-navy); overflow: hidden; }

  .brand {
    position: absolute; display: flex; align-items: center; gap: 14px;
    font-family: "Montserrat", sans-serif; font-weight: 700;
    letter-spacing: 0.14em; line-height: 1.05; font-size: 26px;
    color: var(--navy); right: 60px; top: 70px;
  }
  .brand-mark { width: 40px; height: 40px; background: var(--red); flex: none; }

  .back-mark {
    position: absolute; right: 260px; bottom: 96px;
    width: 52px; height: 52px; background: var(--red);
  }

  .contact {
    position: absolute; left: 60px; top: 200px;
    font-family: "Roboto", sans-serif; color: var(--ink);
  }
  .contact-name {
    font-family: "Montserrat", sans-serif; font-weight: 700;
    font-size: 30px; color: var(--navy);
  }
  .contact-title {
    font-size: 20px; color: var(--red); margin-top: 2px; letter-spacing: 0.02em;
  }
  .contact-line {
    display: flex; align-items: center; gap: 10px;
    font-size: 20px; margin-top: 12px;
  }
  .contact-line + .contact-line { margin-top: 6px; }
  .contact-icon { width: 20px; height: 20px; fill: var(--navy); flex: none; }

  .back-pattern {
    position: absolute; inset: 0;
    background: linear-gradient(135deg, #4a4a8e 0%, #2a2870 45%, #222066 100%);
  }
</style>
</head>
<body>
<main class="canvas">
  <section class="card card-front" aria-label="Card front">
    <div class="brand">
      <span class="brand-mark"></span>
      <span>SPARROW<br>HAULAGE</span>
    </div>
    <div class="contact">
      <p class="contact-name">Martin Obuya</p>
      <p class="contact-title">CEO/FOUNDER</p>
      <p class="contact-line">
        <svg class="contact-icon" viewBox="0 0 24 24" aria-hidden="true"><path d="M6.6 10.8a15.1 15.1 0 0 0 6.6 6.6l2.2-2.2a1 1 0 0 1 1-.25 11.4 11.4 0 0 0 3.6.57 1 1 0 0 1 1 1V20a1 1 0 0 1-1 1A17 17 0 0 1 3 4a1 1 0 0 1 1-1h3.5a1 1 0 0 1 1 1c0 1.25.2 2.45.57 3.57a1 1 0 0 1-.25 1z"/></svg>
        <span>555-206-7142</span>
      </p>
      <p class="contact-line">
        <svg class="contact-icon" viewBox="0 0 24 24" aria-hidden="true"><path d="M2 5h20v14H2z M3.5 6.5 12 13l8.5-6.5" fill="none" stroke="#2b2a6e" stroke-width="2"/></svg>
        <span>martinobuya@sparrow-haulage.example</span>
      </p>
    </div>
  </section>

  <section class="card card-back" aria-label="Card back">
    <div class="back-pattern" role="img" aria-label="Embossed repeating pattern of the brand symbol across the card"></div>
    <span class="back-mark" role="img" aria-label="Brand symbol"></span>
  </section>
</main>
</body>
</html>
```